Varnik Holdings — Business Card Design Brief
Overview
Design a double-sided business card for Varnik Holdings that highlights our two service arms: Varnik Communications (telecommunications) and Varnik Energy (business energy solutions). The card should feel smart and stand out when handed to clients.

Objectives
Showcase our areas of specialty clearly.
Reflect the overall Varnik / Varnik Holdings brand while acknowledging both arms.
Explore using both logos (Communications + Energy) or one unified logo, depending on the design.

Deliverables
One double-sided business card design (front + back).

Content & Copy
Front (preferred): Logo: Varnik / Varnik Holdings
Descriptor: Business Communications | Business Energy
Back:My contact details and company details
Core products: Business Mobile • Telephony • Internet • Business Energy Solutions

Brand & Visual Direction
We have a group logo currently tailored more toward telecoms, plus a separate Varnik Energy logo.
Please explore layouts that use both logos or just one, whichever works best.
Color: I wouldn't mind seeing an option using our the Blue/Purple gradient from our website (varnik-example.co.uk), but also open to non-gradient approaches and other colours..

Overall look: Smart, modern, and distinctive.
Format & Print Specs
Double-sided business card format. (Use a standard size

Must-Haves
Front: Varnik wording or Varnik Holdings wording with atleast 1 logo also on front “Business Communications | Business Energy.”

Back: Contact + company details and core products.
A design that stands out while remaining professional.

Nice-to-Have Options
A gradient version using our site’s Blue/Purple gradient.
A non-gradient version.
A dual-logo treatment versus a single-logo treatment.

Thanks
Owen

```html
<!DOCTYPE html>
<html lang="en">
<head>
<meta charset="utf-8">
<title>Varnik Holdings — Business Card</title>
<link href="https://fonts.googleapis.com/css2?family=Montserrat:wght@700;800&family=Arimo:wght@400&display=swap" rel="stylesheet">
<style>
  :root {
    --backdrop: #e4e4e4;
    --card-light: #ffffff;
    --card-dark: #2f2f2f;
    --navy: #1f1a6b;
    --green: #3aae1c;
    --lime: #a8c81a;
    --blue: #1a7fe0;
    --ink: #2a2a2a;
    --grey-text: #4a4a4a;
    --white: #ffffff;
  }
  * { margin: 0; padding: 0; box-sizing: border-box; }
  html, body { width: 1200px; height: 1200px; overflow: hidden; background: var(--backdrop); }
  .canvas { position: relative; width: 1200px; height: 1200px; }

  .card { position: absolute; width: 689px; height: 393px; }
  .card-front { left: 267px; top: 159px; background: var(--card-light); }
  .card-back { left: 262px; top: 653px; background: var(--card-dark); }

  .brand-word { position: absolute; font-family: "Montserrat", sans-serif; font-weight: 800; line-height: 1; }
  .front-brand { left: 44px; top: 44px; font-size: 64px; color: var(--navy); letter-spacing: -1px; }

  .person-name { position: absolute; left: 44px; top: 133px; font-family: "Montserrat", sans-serif; font-weight: 700; font-size: 26px; color: var(--navy); line-height: 1; }
  .person-role { position: absolute; left: 44px; top: 163px; font-family: "Arimo", sans-serif; font-size: 15px; color: var(--green); }

  .address { position: absolute; left: 44px; top: 196px; font-family: "Arimo", sans-serif; font-size: 16.5px; line-height: 21px; color: var(--grey-text); }

  .contact-list { position: absolute; left: 44px; top: 250px; list-style: none; font-family: "Arimo", sans-serif; font-size: 16.5px; color: var(--grey-text); }
  .contact-list li { display: flex; align-items: center; height: 20.5px; }
  .contact-list svg { width: 14px; height: 14px; margin-right: 12px; fill: var(--navy); }

  .products { position: absolute; left: 48px; top: 343px; font-family: "Arimo", sans-serif; font-size: 17px; color: var(--ink); white-space: nowrap; }

  .front-mark { position: absolute; left: 330px; top: 176px; display: flex; align-items: center; gap: 14px; }
  .mark-circle { border-radius: 50%; border-style: solid; }
  .front-mark .mark-circle { width: 110px; height: 110px; border-width: 8px; border-color: var(--green); }
  .front-mark .mark-name { font-family: "Montserrat", sans-serif; font-weight: 700; font-size: 26px; color: var(--green); }

  .divider { position: absolute; left: 354px; top: 82px; width: 1.5px; height: 228px; background: #9a9a9a; }

  .arm { position: absolute; top: 100px; width: 300px; display: flex; flex-direction: column; align-items: center; }
  .arm-comms { left: 56px; }
  .arm-energy { left: 373px; }
  .arm .mark-circle { width: 100px; height: 100px; border-width: 9px; }
  .arm-comms .mark-circle { border-color: var(--green); }
  .arm-energy .mark-circle { border-color: var(--blue); }
  .arm .brand-word { position: static; margin-top: 20px; font-size: 58px; color: var(--white); letter-spacing: -0.5px; }
  .arm-tagline { margin-top: 12px; font-family: "Arimo", sans-serif; font-size: 17px; white-space: nowrap; }
  .arm-comms .arm-tagline { color: var(--blue); }
  .arm-energy .arm-tagline { color: var(--lime); letter-spacing: 3px; }
</style>
</head>
<body>
<main class="canvas">

  <section class="card card-front" aria-label="Business card front">
    <div class="brand-word front-brand">VARNIK</div>
    <div class="person-name">DANIEL MARSH</div>
    <div class="person-role">President</div>
    <div class="address">412 Alder Court<br>Halbrook, Canada 58210</div>
    <ul class="contact-list">
      <li><svg viewBox="0 0 24 24"><path d="M6.6 10.8a15 15 0 0 0 6.6 6.6l2.2-2.2a1 1 0 0 1 1-.25 11.4 11.4 0 0 0 3.6.57 1 1 0 0 1 1 1V20a1 1 0 0 1-1 1A17 17 0 0 1 3 4a1 1 0 0 1 1-1h3.5a1 1 0 0 1 1 1c0 1.25.2 2.45.57 3.57a1 1 0 0 1-.25 1z"/></svg>555-014-2287</li>
      <li><svg viewBox="0 0 24 24"><path d="M7 1h10a2 2 0 0 1 2 2v18a2 2 0 0 1-2 2H7a2 2 0 0 1-2-2V3a2 2 0 0 1 2-2zm0 3v15h10V4z"/></svg>555-019-6631</li>
      <li><svg viewBox="0 0 24 24"><path d="M2 5h20v14H2zm2 2v.5l8 5 8-5V7zm0 2.8V17h16V9.8l-8 5z"/></svg>info@varnik-example.co.uk</li>
      <li><svg viewBox="0 0 24 24"><path d="M12 2a10 10 0 1 0 0 20 10 10 0 0 0 0-20zm-1 17.9A8 8 0 0 1 4.2 10l4.8 4.8v1a2 2 0 0 0 2 2zm6.9-2.5A2 2 0 0 0 16 16h-1v-3a1 1 0 0 0-1-1H8v-2h2a1 1 0 0 0 1-1V7h2a2 2 0 0 0 2-2v-.4a8 8 0 0 1 2.9 12.8z"/></svg>www.varnik-example.co.uk</li>
    </ul>
    <div class="front-mark">
      <span class="mark-circle" aria-hidden="true"></span>
      <span class="mark-name">Varnik Energy</span>
    </div>
    <p class="products">Business Mobile &nbsp;•&nbsp; Telephony &nbsp;•&nbsp; Internet &nbsp;•&nbsp; Business Energy Solutions</p>
  </section>

  <section class="card card-back" aria-label="Business card back">
    <div class="arm arm-comms">
      <span class="mark-circle" aria-hidden="true"></span>
      <div class="brand-word">VARNIK</div>
      <div class="arm-tagline">BUSINESS COMMUNICATIONS</div>
    </div>
    <div class="divider"></div>
    <div class="arm arm-energy">
      <span class="mark-circle" aria-hidden="true"></span>
      <div class="brand-word">VARNIK</div>
      <div class="arm-tagline">BUSINESS ENERGY</div>
    </div>
  </section>

</main>
</body>
</html>
```